Ferncrest Roam Wording For Logo & Business card

I have the logo, I just need the "Ferncrest Roam" wording to go with it, and a business card design. The only thing on the business card is the website info. We provide nature connection experiences, and bolster these efforts through writing and host a platform for community around it.

I also have an idea of what it could look like (sketch), though I'm really not sure how it would come out. I am open to the best design and happy to consider original artwork. You can see what the site is about at FerncrestRoam.example.

Contact Information for Business Card

The only thing on the business card is the website info and the design. I will put other messaging on the back.

Website lettering (FerncrestRoam.example) in Montserrat

Logo Text

Ferncrest Roam (letters optional)

Font styles to use
Other font styles liked:
• montserrat

```html
<!DOCTYPE html>
<html lang="en">
<head>
<meta charset="utf-8">
<title>Ferncrest Roam — Business Card</title>
<link rel="stylesheet" href="https://fonts.googleapis.com/css2?family=Montserrat:wght@400;500;600&display=swap">
<style>
  :root {
    --backdrop: #d9d9dc;
    --purple-deep: #150726;
    --purple-mid: #2c1545;
    --purple-light: #52305f;
    --orange: #f28a12;
    --ink-light: #f1eff5;
    --silver: #e4e2ea;
    --badge-bg: #fbf7ef;
    --badge-ink: #2a1240;
  }
  * { box-sizing: border-box; margin: 0; padding: 0; }
  html, body { width: 1200px; height: 800px; overflow: hidden; }
  body {
    background: var(--backdrop);
    font-family: "Montserrat", sans-serif;
    display: flex;
    align-items: center;
    justify-content: center;
    gap: 40px;
  }
  .card {
    position: relative;
    width: 560px;
    height: 320px;
    border-radius: 22px;
    background: linear-gradient(200deg, var(--purple-light) 0%, var(--purple-mid) 45%, var(--purple-deep) 100%);
    box-shadow: 0 14px 30px rgba(0,0,0,0.25);
    overflow: hidden;
    color: var(--ink-light);
  }

  /* Divider placeholder: flat band where the ornamental divider sits */
  .divider-band {
    display: block;
    height: 3px;
    border-radius: 2px;
    background: var(--orange);
    opacity: 0.7;
  }

  /* Front */
  .contact {
    position: absolute;
    left: 36px;
    bottom: 38px;
    width: 270px;
  }
  .contact-name { color: var(--orange); font-size: 24px; font-weight: 500; letter-spacing: 0.5px; }
  .contact-role { font-size: 14px; margin-top: 2px; }
  .contact .divider-band { width: 60px; margin: 12px 0; }
  .contact-line { display: flex; align-items: center; gap: 10px; font-size: 13px; margin: 5px 0; }
  .contact-line svg { flex: none; }
  .contact-web { color: var(--orange); font-size: 14px; }
  .front-badge {
    position: absolute;
    right: 30px;
    top: 50%;
    transform: translateY(-50%);
    width: 220px;
    height: 220px;
    border-radius: 50%;
    background: var(--badge-bg);
    display: flex;
    align-items: center;
    justify-content: center;
    text-align: center;
  }
  .front-badge-name {
    color: var(--badge-ink);
    font-size: 22px;
    font-weight: 500;
    letter-spacing: 2px;
    line-height: 1.3;
  }

  /* Back */
  .brand {
    position: absolute;
    left: 56px;
    top: 110px;
    display: flex;
    align-items: center;
    gap: 18px;
  }
  .brand-dot {
    width: 60px;
    height: 60px;
    border-radius: 50%;
    background: var(--orange);
  }
  .brand-name {
    color: var(--silver);
    font-size: 34px;
    font-weight: 500;
    letter-spacing: 3px;
    white-space: nowrap;
  }
  .web-row {
    position: absolute;
    left: 30px;
    right: 30px;
    bottom: 62px;
    display: flex;
    align-items: center;
    gap: 12px;
  }
  .web-row .divider-band { flex: 1; height: 2px; }
  .web-row-url { font-size: 16px; letter-spacing: 1px; color: var(--ink-light); white-space: nowrap; }
</style>
</head>
<body>

<section class="card card-front">
  <div class="contact">
    <p class="contact-name">Daniel Hart</p>
    <p class="contact-role">President</p>
    <span class="divider-band" role="img" aria-label="Orange decorative divider"></span>
    <p class="contact-line">
      <svg width="12" height="14" viewBox="0 0 12 14"><rect x="1.5" y="0.8" width="9" height="12.4" rx="1.6" fill="none" stroke="var(--orange)" stroke-width="1.4"/><line x1="4.5" y1="11" x2="7.5" y2="11" stroke="var(--orange)" stroke-width="1.2"/></svg>
      555-014-2290
    </p>
    <p class="contact-line">
      <svg width="14" height="12" viewBox="0 0 14 12"><rect x="0.8" y="1.2" width="12.4" height="9.6" rx="1" fill="var(--orange)"/><polyline points="1.2,2 7,6.6 12.8,2" fill="none" stroke="var(--purple-deep)" stroke-width="1.2"/></svg>
      info@ferncrestroam.example
    </p>
    <span class="divider-band" role="img" aria-label="Orange decorative divider"></span>
    <p class="contact-web">www.ferncrestroam.example</p>
  </div>
  <div class="front-badge">
    <p class="front-badge-name">FERNCREST<br>ROAM</p>
  </div>
</section>

<section class="card card-back">
  <div class="brand">
    <span class="brand-dot"></span>
    <p class="brand-name">FERNCREST ROAM</p>
  </div>
  <div class="web-row">
    <span class="divider-band" role="img" aria-label="Orange decorative divider"></span>
    <p class="web-row-url">www.FerncrestRoam.example</p>
    <span class="divider-band" role="img" aria-label="Orange decorative divider"></span>
  </div>
</section>

</body>
</html>
```